Moxy Fen needs some awesome stationary

Do you have what it takes to get my brand? You either do or you don't, have a crack at a design and you my just win my business.

I don't want to waste your or my time, so put your creative genius on either a business card or envelope.

I however need a package of stationary that follows the same brand. I will message you to complete the remaining should I like your first submission.

Here is what I need, have a go!

Basically I need the following for my small business based in melbourne.
- Letterhead (printer ready and MS Word)
- Business Card
- Compliments Slip
- Envelope
- Proposal Cover Page (MS Word only)
- Presentation Folder
- Marbled Fox Cards
- Student Name Tent
- Index Cards
- Vell-Ka

I am establishing the brand and it must be modern, professional but also relaxed; that is not formal and not corporate. It represents a company are leaders, but small enough to care and operate like a bunch of friends. We are bringing people and conversations back to business, and turfing out all the bureaucracy and crazy and wasteful procedures. Its about "lets talk and figure it out together and find even better ways".

Target Market(s)

Mainly companies that build software products, but Agile practices are used in many other industries (even graphic design projects)

Industry/Entity Type

Information Technology

Font styles to use
Sans Serif

Colors
3176b5
aaaaaa

Requirements
Must have
• I like curves and circles and not boxes or rectangles.
• I want a colour rich design with my brand colours, but it must be balanced.
• I want more modern than traditional, but simple modern
Should not have
• Not corporate
• Please don't waste my time if your not going to think about it.
• Don't mess with my primary logo
• Don't change my colours
• Don't overlay logo on image

```html
<!DOCTYPE html>
<html lang="en">
<head>
<meta charset="utf-8">
<title>Moxy Fen — Index Cards</title>
<link href="https://fonts.googleapis.com/css2?family=Open+Sans:wght@400;700&display=swap" rel="stylesheet">
<style>
  :root {
    --backdrop: #898a8e;
    --paper: #ffffff;
    --rule-solid: #666666;
    --rule-dotted: #9a9a9a;
    --ink: #555555;
    --brand-ink: #222222;
    --coral: #ff807c;
    --butter: #ffe585;
    --leaf: #5dd362;
    --sky: #36aac8;
    --violet: #8d61d3;
  }
  * { box-sizing: border-box; margin: 0; padding: 0; }
  html, body {
    width: 1200px; height: 902px; overflow: hidden;
    background: var(--backdrop);
    font-family: "Open Sans", Arial, sans-serif;
  }
  .sheet { position: relative; width: 1200px; height: 902px; }
  .index-card {
    position: absolute;
    width: 344px; height: 386px;
    background: var(--paper);
    box-shadow: 0 1px 3px rgba(0,0,0,0.25);
    overflow: hidden;
  }
  .index-card--a { left: 58px;  top: 55px; }
  .index-card--b { left: 417px; top: 55px; }
  .index-card--c { left: 784px; top: 55px; }
  .index-card--d { left: 58px;  top: 458px; }
  .index-card--e { left: 417px; top: 458px; }
  .index-card--f { left: 784px; top: 458px; }

  .title-band {
    height: 61px;
    border-bottom: 1px solid var(--rule-solid);
  }
  .title-band--coral  { background: var(--coral); }
  .title-band--butter { background: var(--butter); }
  .title-band--leaf   { background: var(--leaf); }
  .title-band--sky    { background: var(--sky); }
  .title-band--violet { background: var(--violet); }
  .title-band--plain  { background: var(--paper); }

  .writing-line {
    position: absolute; left: 0; right: 0;
    border-top: 1px dotted var(--rule-dotted);
  }
  .writing-line--1 { top: 110px; }
  .writing-line--2 { top: 152px; }
  .writing-line--3 { top: 195px; }
  .writing-line--4 { top: 238px; }
  .writing-line--5 { top: 280px; }

  .footer-rule {
    position: absolute; left: 0; right: 0; top: 322px;
    border-top: 1px solid var(--rule-solid);
  }
  .estimate-circle {
    position: absolute; left: 259px; top: 312px;
    width: 70px; height: 70px; border-radius: 50%;
    border: 2px solid var(--ink);
    background: var(--paper);
  }
  .brand-mark {
    position: absolute; left: 9px; top: 368px;
    display: flex; align-items: center; gap: 3px;
    font-size: 8px; font-weight: 700; color: var(--brand-ink);
    line-height: 1;
  }
  .brand-mark__dot {
    width: 7px; height: 7px; border-radius: 50%;
    background: var(--brand-ink);
  }
  .tagline {
    position: absolute; left: 152px; top: 372px;
    font-size: 6px; color: var(--ink); line-height: 1;
  }
</style>
</head>
<body>
<main class="sheet">
  <section class="index-card index-card--a">
    <div class="title-band title-band--coral"></div>
    <div class="writing-line writing-line--1"></div><div class="writing-line writing-line--2"></div><div class="writing-line writing-line--3"></div><div class="writing-line writing-line--4"></div><div class="writing-line writing-line--5"></div>
    <div class="footer-rule"></div><div class="estimate-circle"></div>
    <div class="brand-mark"><span class="brand-mark__dot"></span>Moxy Fen</div>
    <div class="tagline">Get It done</div>
  </section>
  <section class="index-card index-card--b">
    <div class="title-band title-band--butter"></div>
    <div class="writing-line writing-line--1"></div><div class="writing-line writing-line--2"></div><div class="writing-line writing-line--3"></div><div class="writing-line writing-line--4"></div><div class="writing-line writing-line--5"></div>
    <div class="footer-rule"></div><div class="estimate-circle"></div>
    <div class="brand-mark"><span class="brand-mark__dot"></span>Moxy Fen</div>
    <div class="tagline">Get It done</div>
  </section>
  <section class="index-card index-card--c">
    <div class="title-band title-band--leaf"></div>
    <div class="writing-line writing-line--1"></div><div class="writing-line writing-line--2"></div><div class="writing-line writing-line--3"></div><div class="writing-line writing-line--4"></div><div class="writing-line writing-line--5"></div>
    <div class="footer-rule"></div><div class="estimate-circle"></div>
    <div class="brand-mark"><span class="brand-mark__dot"></span>Moxy Fen</div>
    <div class="tagline">Get It done</div>
  </section>
  <section class="index-card index-card--d">
    <div class="title-band title-band--sky"></div>
    <div class="writing-line writing-line--1"></div><div class="writing-line writing-line--2"></div><div class="writing-line writing-line--3"></div><div class="writing-line writing-line--4"></div><div class="writing-line writing-line--5"></div>
    <div class="footer-rule"></div><div class="estimate-circle"></div>
    <div class="brand-mark"><span class="brand-mark__dot"></span>Moxy Fen</div>
    <div class="tagline">Get It done</div>
  </section>
  <section class="index-card index-card--e">
    <div class="title-band title-band--violet"></div>
    <div class="writing-line writing-line--1"></div><div class="writing-line writing-line--2"></div><div class="writing-line writing-line--3"></div><div class="writing-line writing-line--4"></div><div class="writing-line writing-line--5"></div>
    <div class="footer-rule"></div><div class="estimate-circle"></div>
    <div class="brand-mark"><span class="brand-mark__dot"></span>Moxy Fen</div>
    <div class="tagline">Get It done</div>
  </section>
  <section class="index-card index-card--f">
    <div class="title-band title-band--plain"></div>
    <div class="writing-line writing-line--1"></div><div class="writing-line writing-line--2"></div><div class="writing-line writing-line--3"></div><div class="writing-line writing-line--4"></div><div class="writing-line writing-line--5"></div>
    <div class="footer-rule"></div><div class="estimate-circle"></div>
    <div class="brand-mark"><span class="brand-mark__dot"></span>Moxy Fen</div>
    <div class="tagline">Get It done</div>
  </section>
</main>
</body>
</html>
```